Casino with the 'highest winning percentage' needs a stationery design

This is for a casino in Colombo, Sri Lanka and we need a stationery design for business card, letter head and envelope.

Should be very professional, simple and elegant without fancy fonts

Reason: Not fully satisfied with the designs. Need more designs.

Business

• 1. card deck symbol 'CLUBS' in red, or black

2. name in BLOCK CAPITAL LETTERS

3. Preferred font colours are black, white or red

4. Prefer 'professional /elegant' fonts
• SHOULD NOT HAVE ANY OTHER SYMBOL EXCEPT 'CLUBS'

DO NOT PREFER ITALIC FONTS

```html
<!DOCTYPE html>
<html lang="en">
<head>
<meta charset="utf-8">
<title>Corvel Entertainment – Business Card</title>
<link rel="stylesheet" href="https://fonts.googleapis.com/css2?family=Caladea:wght@400;700&display=swap">
<style>
  :root {
    --backdrop: #eeeae6;
    --paper: #ffffff;
    --ink: #111111;
    --brand-red: #d5323b;
    --tagline-red: #c8333a;
    --on-red: #ffffff;
    --suit-grey: #e2e2e2;
    --suit-peach: #fbe6dc;
  }
  * { margin: 0; padding: 0; box-sizing: border-box; }
  html, body { width: 1200px; height: 372px; overflow: hidden; }
  body {
    background: var(--backdrop);
    font-family: "Caladea", Georgia, serif;
    color: var(--ink);
    position: relative;
  }
  .card {
    position: absolute;
    top: 26px;
    width: 556px;
    height: 316px;
    background: var(--paper);
    overflow: hidden;
  }
  .card--front { left: 30px; }
  .card--back { left: 615px; }

  /* Front */
  .brand-mark {
    position: absolute;
    left: 112px;
    top: 44px;
    width: 72px;
    height: 72px;
    border-radius: 50%;
    background: var(--brand-red);
  }
  .brand-name {
    position: absolute;
    left: 211px;
    top: 42px;
    font-weight: 700;
    font-size: 28px;
    line-height: 39px;
    letter-spacing: 0.5px;
    white-space: nowrap;
  }
  .tagline {
    position: absolute;
    left: 0;
    width: 100%;
    top: 158px;
    text-align: center;
    font-weight: 700;
    font-size: 12.5px;
    line-height: 16px;
    letter-spacing: 1.3px;
    color: var(--tagline-red);
  }
  .rule {
    position: absolute;
    left: 0;
    width: 100%;
    top: 184px;
    height: 3px;
    background: var(--ink);
  }
  .contact-band {
    position: absolute;
    left: 0;
    width: 100%;
    top: 190px;
    height: 126px;
    background: var(--brand-red);
    color: var(--on-red);
  }
  .company {
    position: absolute;
    right: 300px;
    top: 24px;
    text-align: right;
    font-style: normal;
    font-size: 13px;
    line-height: 19px;
    white-space: nowrap;
  }
  .company__name {
    font-weight: 700;
    font-size: 17px;
    line-height: 22px;
    margin-bottom: 4px;
  }
  .divider {
    position: absolute;
    left: 273px;
    top: 13px;
    width: 1px;
    height: 102px;
    background: var(--on-red);
  }
  .contact-list {
    position: absolute;
    left: 287px;
    top: 11px;
    list-style: none;
    font-size: 13px;
    line-height: 20.5px;
    white-space: nowrap;
  }
  .contact-list li { display: flex; align-items: center; gap: 7px; }
  .contact-list svg { width: 11px; height: 11px; fill: var(--on-red); flex: none; }

  /* Back */
  .suit-backdrop {
    position: absolute;
    left: 133px;
    top: 14px;
    width: 292px;
    height: 289px;
    background: linear-gradient(135deg, var(--suit-grey) 0%, var(--suit-peach) 50%, var(--suit-grey) 100%);
    opacity: 0.45;
  }
  .back-title {
    position: absolute;
    left: 0;
    width: 100%;
    top: 102px;
    text-align: center;
    font-weight: 700;
    font-size: 47px;
    line-height: 53px;
    letter-spacing: 0.5px;
    white-space: nowrap;
  }
  .back-city {
    position: absolute;
    left: 0;
    width: 100%;
    top: 212px;
    text-align: center;
    font-weight: 700;
    font-size: 34px;
    line-height: 38px;
  }
</style>
</head>
<body>
  <section class="card card--front">
    <span class="brand-mark"></span>
    <h1 class="brand-name">CORVEL’S<br>ENTERTAINMENT</h1>
    <p class="tagline">Highest Winning Percentage In The World</p>
    <div class="rule"></div>
    <div class="contact-band">
      <address class="company">
        <div class="company__name">CORVEL LIMITED</div>
        58, Lotus Garden Road<br>
        Colombo 00300<br>
        Sri Lanka
      </address>
      <div class="divider"></div>
      <ul class="contact-list">
        <li><svg viewBox="0 0 12 12"><path d="M2.5 1l2 2.2-1 1.3a6 6 0 0 0 4 4l1.3-1 2.2 2-1.3 1.5C5.5 11 1 6.5 1 2.3z"/></svg>+ 94 11 2450738</li>
        <li><svg viewBox="0 0 12 12"><path d="M3.5 0h5a1 1 0 0 1 1 1v10a1 1 0 0 1-1 1h-5a1 1 0 0 1-1-1V1a1 1 0 0 1 1-1zm.5 2v6h4V2zm2 7.2a.8.8 0 1 0 0 1.6.8.8 0 0 0 0-1.6z"/></svg>+ 94 77 5120946</li>
        <li><svg viewBox="0 0 12 12"><path d="M3 1h5v3H3zM1 5h10v5H1zm2 1.5v1h2v-1zm4 0v1h2v-1z"/></svg>+ 94 11 2450739</li>
        <li><svg viewBox="0 0 12 12"><path d="M0 3h12v7H0zm1 1l5 3.3L11 4v-.2H1z"/></svg>info@corvelcolombo.com</li>
        <li><svg viewBox="0 0 12 12"><path d="M6 0a6 6 0 1 0 0 12A6 6 0 0 0 6 0zm0 1.3c.8.8 1.3 2.2 1.4 4H4.6c.1-1.8.6-3.2 1.4-4zM1.3 6.7h2c.1 1.5.5 2.8 1.1 3.7a4.8 4.8 0 0 1-3.1-3.7zm0-1.4a4.8 4.8 0 0 1 3.1-3.7c-.6.9-1 2.2-1.1 3.7zm3.3 1.4h2.8c-.1 1.7-.6 3.1-1.4 4-.8-.9-1.3-2.300-1.4-4zm4.1 0h2a4.8 4.8 0 0 1-3.1 3.7c.6-.9 1-2.2 1.1-3.7zm0-1.4c-.1-1.5-.5-2.8-1.1-3.7a4.8 4.8 0 0 1 3.1 3.7z"/></svg>www.corvelcolombo.com</li>
      </ul>
    </div>
  </section>

  <section class="card card--back">
    <div class="suit-backdrop" role="img" aria-label="Faint playing-card suit symbols in grey and peach"></div>
    <h2 class="back-title">CORVEL’S<br>ENTERTAINMENT</h2>
    <p class="back-city">Colombo</p>
  </section>
</body>
</html>
```